Web Design Project for a beach town business owner who supports new families with their babies.

I'm looking for a basic website with the following pages: home, about, services, FAQs, blog, and contact page. I have images and content ready to go.

Target Market(s)

Men and women between the ages of 22 and 42, growing families

Industry/Entity Type

Postpartum Doula

Coding

Number of Pages Required

Font styles to use
Serif
Other font styles liked:
• My logo font is "Nexa Bold" - so coordinating fonts with that are ideal

Colors
00AB8E
00BBA5
67D7C9
C6EFE9
E9F9F6
EE7325
F08F49
F5BC92
FAE3D3
FDF4ED

Requirements
Must have
• Warm and professional vibe, multicultural images, aligned with my branding colors and font ("Nexa Bold"; COLORS: light blue hex: #2FCEC2 R: 47 G: 206 B: 194 dark blue hex: #007C7C R: 0 G: 124 B: 124 orange hex: #F77B4E R: 247 G: 123 B: 78), good SEO
Should not have
• Ultra feminine images, baby bottles, cutesy images.

```html
<!DOCTYPE html>
<html lang="en">
<head>
<meta charset="utf-8">
<title>Harborlight Families Postpartum Care</title>
<link rel="stylesheet" href="https://fonts.googleapis.com/css2?family=Montserrat:wght@500;600;700;800&family=Nunito:wght@400;600;700&display=swap">
<style>
:root{
  --teal:#2FCEC2;
  --teal-deep:#007C7C;
  --orange:#F77B4E;
  --orange-soft:#F08F49;
  --ink:#222;
  --body:#444;
  --field:#fff;
  --line:#d9d9d9;
  --pale:#f7f7f7;
  --grey-bg:#eeeeee;
}
*{box-sizing:border-box;margin:0;padding:0}
html,body{width:1200px;height:3859px;overflow:hidden;background:#fff}
body{position:relative;font-family:"Nunito",sans-serif;color:var(--body)}
.abs{position:absolute}
.heading{font-family:"Montserrat",sans-serif;font-weight:700}
.btn{position:absolute;display:flex;align-items:center;justify-content:center;border-radius:26px;background:var(--orange);color:#fff;font-family:"Montserrat",sans-serif;font-weight:600;font-size:16px;letter-spacing:.5px;text-transform:uppercase}
.btn.teal{background:var(--teal)}
.section-title{position:absolute;left:0;width:1200px;text-align:center;font-family:"Montserrat",sans-serif;font-weight:700;font-size:34px;letter-spacing:.5px;text-transform:uppercase}
.section-title .t{color:var(--teal)} .section-title .o{color:var(--orange)}
.rule{position:absolute;left:587px;width:26px;height:3px;background:var(--orange)}

/* header */
.site-header{top:0;left:0;width:1200px;height:69px;background:#fff;z-index:5}
.brand{position:absolute;left:123px;top:0;width:144px;height:138px;border-radius:50%;background:#fff;box-shadow:0 2px 6px rgba(0,0,0,.15);display:flex;align-items:center;justify-content:center;z-index:6}
.brand span{font-family:"Montserrat",sans-serif;font-weight:700;font-size:15px;color:var(--teal-deep)}
.nav a{position:absolute;top:29px;font-family:"Montserrat",sans-serif;font-weight:600;font-size:13px;color:var(--ink);text-decoration:none}
.phone{position:absolute;left:890px;top:20px;font-family:"Montserrat",sans-serif;font-weight:600;font-size:25px;color:var(--teal)}

/* hero */
.hero-photo{top:69px;left:0;width:1200px;height:620px;background:radial-gradient(ellipse at 78% 40%,#a86f56 0,#6f6b48 22%,#3f5a2a 45%,#2c4420 70%,#243a1c 100%)}
.hero-eyebrow{left:132px;top:241px;font-family:"Montserrat",sans-serif;font-weight:600;font-size:15px;color:var(--teal)}
.hero-title{left:128px;top:277px;font-family:"Montserrat",sans-serif;font-weight:800;font-size:62px;color:#fff}
.hero-text{left:132px;top:372px;width:520px;font-size:14px;line-height:28px;color:#eee}

/* about */
.about-text{left:162px;top:817px;width:876px;text-align:center;font-size:13px;line-height:28px;color:var(--body)}
.about-cta{left:0;top:1057px;width:1200px;text-align:center;font-size:14px;font-weight:600;color:var(--orange)}

/* services */
.svc-sub{left:0;width:1200px;text-align:center;color:#fff}
.svc{position:absolute;width:200px;text-align:center}
.svc .ic{margin:0 auto;width:126px;height:126px;border-radius:50%;background:var(--teal);box-shadow:0 0 0 5px rgba(47,206,194,.35)}
.svc p{margin-top:22px;font-family:"Montserrat",sans-serif;font-weight:600;font-size:15px;line-height:28px;color:#fff}

/* faq */
.faq{position:absolute;left:189px;width:824px;height:57px;background:var(--pale);border-radius:4px;display:flex;justify-content:space-between;align-items:center;padding:0 30px 0 24px;font-family:"Montserrat",sans-serif;font-weight:700;font-size:13px;color:var(--ink)}
.faq-answer{left:211px;top:2081px;width:760px;font-size:13px;line-height:29px}

/* contact */
.contact-bg{left:0;top:2527px;width:1200px;height:1080px;background:linear-gradient(180deg,#ededed,#f4f4f4 60%,#ececec)}
.field{position:absolute;background:var(--field);border:1px solid var(--line);font-size:12px;color:#555;padding:14px 11px}
.field.sel::after{content:"";position:absolute;right:14px;top:20px;border:4px solid transparent;border-top:5px solid #333}
.q{position:absolute;left:268px;font-size:13px;color:#444}
.check{position:absolute;font-size:12px;font-weight:700;color:#333;display:flex;align-items:center;gap:8px}
.check i{display:inline-block;width:13px;height:13px;background:#ddd}

/* footer */
.foot-nav a{position:absolute;top:3710px;font-family:"Montserrat",sans-serif;font-weight:700;font-size:13px;color:#fff;text-decoration:none}
.social{position:absolute;top:3751px;width:30px;height:30px;border-radius:50%;background:var(--orange)}
.copy{left:0;top:3802px;width:1200px;text-align:center;font-family:"Montserrat",sans-serif;font-weight:700;font-size:12px;color:#fff}
.copy b{color:var(--teal);font-weight:700}
</style>
</head>
<body>

<!-- Header -->
<header class="abs site-header">
  <div class="brand"><span>Harborlight</span></div>
  <nav class="nav">
    <a style="left:337px">HOME</a>
    <a style="left:410px">ABOUT US</a>
    <a style="left:514px">SERVICES</a>
    <a style="left:615px">FAQS</a>
    <a style="left:685px">BLOG</a>
    <a style="left:756px">CONTACT US</a>
  </nav>
  <div class="phone">+123 456 7890</div>
</header>

<!-- Hero -->
<div class="abs hero-photo" role="img" aria-label="Portrait of the postpartum care expert smiling outdoors in front of soft green foliage"></div>
<svg class="abs" style="left:0;top:0" width="1200" height="700" viewBox="0 0 1200 700">
  <path d="M0 558 Q600 778 1200 558 L1200 700 L0 700 Z" fill="#fff"/>
  <path d="M0 562 Q600 788 1200 562" fill="none" stroke="var(--teal)" stroke-width="3"/>
</svg>
<p class="abs hero-eyebrow">WELCOME TO HARBORLIGHT FAMILIES POSTPARTUM CARE!</p>
<h1 class="abs hero-title">HI, I’M LENA WARD</h1>
<p class="abs hero-text">&nbsp;a certified postpartum care expert and educator serving families of all varieties in the greater San Diego area and beyond.</p>
<a class="btn" style="left:132px;top:443px;width:170px;height:50px">Get Started</a>

<!-- About -->
<div class="abs" style="left:420px;top:760px;width:360px;height:360px;border-radius:50%;border:14px solid rgba(47,206,194,.05)"></div>
<h2 class="section-title" style="top:744px"><span class="t">ABOUT</span> <span class="o">ME</span></h2>
<div class="rule" style="top:790px"></div>
<p class="abs about-text">Lena (she/her/hers) is a former Keystone certified birth advocate and support provider (also known as a doula) and childbirth educator who has supported over 200 growing families between the years 2015 and 2021. She received her Bachelor of Arts in Liberal Studies with an emphasis on Spanish and a lifetime teaching credential from Bayview State University in the year 2000 – providing her with a deep understanding of child growth and development and educational theory and techniques. &nbsp;She had a blast teaching first through fourth grade students from 2000-2012 in the San Francisco Bay Area. She currently lives on the traditional, ancestral, and unceded land of the Kumeyaay Nation and its peoples, also known as San Diego County, with her wife, daughter, and four fur babies. She spends her days off taking action to protect reproductive rights and advance racial and social justice, hanging out at the beach with her pups and her family, getting her hands dirty in her succulent garden, or snuggling up with a good book and a cup of chai.</p>
<p class="abs about-cta">Contact me today to schedule a free consultation.</p>
<a class="btn" style="left:514px;top:1093px;width:171px;height:50px">Learn More</a>

<!-- Services -->
<svg class="abs" style="left:0;top:1200px" width="1200" height="700" viewBox="0 0 1200 700" role="img" aria-label="Warm orange-toned photo of smiling parents with their newborn">
  <defs>
    <linearGradient id="svcFill" x1="0" x2="1" y1="0" y2="0">
      <stop offset="0" stop-color="#f08a5d"/><stop offset=".5" stop-color="#f27f52"/><stop offset="1" stop-color="#ef8a5e"/>
    </linearGradient>
  </defs>
  <path d="M0 100 Q600 -56 1200 100 L1200 580 Q600 720 0 580 Z" fill="url(#svcFill)"/>
  <path d="M0 89 Q600 -70 1200 89" fill="none" stroke="var(--teal)" stroke-width="3"/>
  <path d="M0 591 Q600 733 1200 591" fill="none" stroke="var(--teal)" stroke-width="3"/>
</svg>
<h2 class="section-title" style="top:1300px;color:#fff">OUR SERVICES</h2>
<p class="abs svc-sub heading" style="top:1362px;font-size:14px;font-weight:600">What does a typical postpartum care shift look like?</p>
<p class="abs svc-sub" style="top:1395px;font-size:12px">I will come to you. I will meet you where you are on your parenting journey.</p>
<p class="abs svc-sub" style="top:1422px;font-size:12px">You do not have to dry your tears, get out of your pajamas, brush your hair or teeth, take a shower, or clean your house before I arrive.</p>
<div class="svc" style="left:101px;top:1477px"><div class="ic" role="img" aria-label="Tidy living space icon"></div><p>Tidy up common<br>living space</p></div>
<div class="svc" style="left:301px;top:1477px"><div class="ic" role="img" aria-label="Laundry icon"></div><p>Wash and fold<br>laundry</p></div>
<div class="svc" style="left:501px;top:1477px"><div class="ic" role="img" aria-label="Dishwasher icon"></div><p>Load/unload<br>dishwasher</p></div>
<div class="svc" style="left:700px;top:1477px"><div class="ic" role="img" aria-label="Checklist icon"></div><p>Organize baby supplies<br>/nursery</p></div>
<div class="svc" style="left:901px;top:1477px"><div class="ic" role="img" aria-label="Spray bottle icon"></div><p>Sanitize baby<br>bottles</p></div>
<a class="btn teal" style="left:497px;top:1718px;width:204px;height:50px">View All Services</a>

<!-- FAQ -->
<h2 class="section-title" style="top:1924px"><span class="t">FREQUENTLY</span> <span class="o">ASKED QUESTIONS</span></h2>
<div class="rule" style="top:1970px"></div>
<div class="faq" style="top:2007px"><span>ARE YOU AVAILABLE FOR OVERNIGHT SHIFTS?</span><span>-</span></div>
<p class="abs faq-answer">My service hours are between 9:00am and 4:00pm, so I can be home with our kiddo in the evenings. I am happy to refer you to my favorite postpartum colleagues who provide overnight care.</p>
<div class="faq" style="top:2154px"><span>WHAT IS A POSTPARTUM CARE EXPERT (DOULA)?</span><span>+</span></div>
<div class="faq" style="top:2233px"><span>DO YOU PROVIDE NANNY SERVICES?</span><span>+</span></div>
<div class="faq" style="top:2311px"><span>WHAT KINDS OF MEDICAL SUPPORT CAN YOU OFFER?</span><span>+</span></div>
<div class="faq" style="top:2391px"><span>ARE THERE ANY SERVICES YOU DON’T PROVIDE?</span><span>+</span></div>

<!-- Contact -->
<div class="abs contact-bg" role="img" aria-label="Faded grey photo of a parent holding a baby"></div>
<h2 class="section-title" style="top:2599px"><span class="t">GET</span> <span class="o">IN TOUCH</span></h2>
<div class="rule" style="top:2645px"></div>
<p class="abs" style="left:0;top:2666px;width:1200px;text-align:center;font-size:13px">Your anchor is just a message away!</p>
<p class="abs" style="left:0;top:2695px;width:1200px;text-align:center;font-size:13px">Contact me today to schedule a no-pressure, free consultation to see if we’re a good fit for your needs.</p>
<div class="field" style="left:268px;top:2749px;width:325px;height:45px">Full Name *</div>
<div class="field" style="left:607px;top:2749px;width:325px;height:45px">Email Address *</div>
<div class="field" style="left:268px;top:2806px;width:664px;height:45px">Phone Number *</div>
<p class="q" style="top:2864px">Have you had your baby(ies), yet?</p>
<span class="check" style="left:268px;top:2895px"><i></i>Yes</span>
<span class="check" style="left:326px;top:2895px"><i></i>No</span>
<div class="field sel" style="left:268px;top:2923px;width:325px;height:45px">If so, did you have?</div>
<div class="field sel" style="left:607px;top:2923px;width:325px;height:45px">If not, what is your EDD?</div>
<p class="q" style="top:2984px">Is this your first baby?</p>
<span class="check" style="left:268px;top:3015px"><i></i>Yes</span>
<span class="check" style="left:326px;top:3015px"><i></i>No</span>
<div class="field" style="left:268px;top:3045px;width:664px;height:78px">If not, what are the ages of your older children?</div>
<div class="field sel" style="left:268px;top:3138px;width:664px;height:45px">Are you interested in in-person or virtual support?*</div>
<div class="field" style="left:268px;top:3198px;width:664px;height:110px">I’d just like to add</div>
<a class="btn" style="left:514px;top:3335px;width:171px;height:49px">Submit</a>

<!-- Footer -->
<svg class="abs" style="left:0;top:3380px" width="1200" height="479" viewBox="0 0 1200 479">
  <path d="M0 200 Q600 20 1200 200 L1200 479 L0 479 Z" fill="#000"/>
  <path d="M0 188 Q600 6 1200 188" fill="none" stroke="var(--teal)" stroke-width="3"/>
</svg>
<div class="brand" style="left:534px;top:3552px;width:132px;height:132px;top:3552px;box-shadow:none"><span>Harborlight</span></div>
<nav class="foot-nav">
  <a style="left:346px">HOME</a>
  <a style="left:420px">ABOUT US</a>
  <a style="left:524px">SERVICES</a>
  <a style="left:624px">FAQS</a>
  <a style="left:695px">BLOG</a>
  <a style="left:766px">CONTACT US</a>
</nav>
<span class="social" style="left:518px" aria-label="Social link"></span>
<span class="social" style="left:563px" aria-label="Social link"></span>
<span class="social" style="left:607px" aria-label="Social link"></span>
<span class="social" style="left:651px" aria-label="Social link"></span>
<p class="abs copy">© Copyright © 2021 <b>Harborlight Families Postpartum Care</b> All rights reserved.</p>

</body>
</html>
```